Healthcare/Medical Consultant Company

QRN is a Healthcare Conultant Company. We help doctors manage the business side of their medical practice.
We already have a very basic world press design. We want an upgraded design that conveys partnership, healthcare expertise and healthcare innovation to our client. It needs to have a sleek, clean, modern and inclusive look. Pictures need need to convey diversity (including pictures of people of all races and shows both men and women working together in a healthcare environment to make it better). The Pictures on the home page should particularly illustrate diversity and Healthcare expertise. The company logo is blue and white but the site doesn’t have to follow the exact same theme but the logo needs to blend well with the chosen theme. The logo should ideally be in the header of the website. We would also like the following included in our website:

1. Pages should include: a home page, About Us page, Services page, Get a quote page, Contact Us page, Staff page(where we can add pictures and bio for staff).

2. The Drop down menu for services should have hyperlinks ( for each service)Leading to a page that provides detailed info about that specific service. Our services include: Revenue Cycle Management, Regulatory Compliance, Human Resources Management, & practice Management.

3. Links to social media should in the header or footer of each page.

4. Contact info should be in the footer of each page.

5. Clients should be an email to us from the contact page.

Target Market(s)

Physician Medical Practices

Industry/Entity Type

Medical

Coding

Coded - Design and coding required

Font styles to use
Sans Serif

Colors

Designer to choose colors to be used in the design.

Requirements
Must have
• See project description
Nice to have
• See project description

```html
<!DOCTYPE html>
<html lang="en">
<head>
<meta charset="utf-8">
<title>QRN Health Partners – Advancing Healthcare</title>
<link rel="stylesheet" href="https://fonts.googleapis.com/css2?family=Cinzel:wght@400;700&family=Open+Sans:wght@400;600;700&display=swap">
<style>
:root{
  --navy:#0a3b8f;
  --navy-deep:#08337f;
  --accent:#2b8fd0;
  --accent-dark:#1f7dbd;
  --ink:#1e1e1e;
  --text:#555b61;
  --muted:#7c8590;
  --pale:#f2fafc;
  --line:#c9dbe2;
  --white:#ffffff;
}
*{box-sizing:border-box;margin:0;padding:0}
html,body{width:1200px;height:3041px;overflow:hidden}
body{position:relative;background:var(--white);font-family:"Open Sans",Arial,sans-serif;color:var(--text)}
.abs{position:absolute}
.serif{font-family:"Cinzel",Georgia,serif}

/* header */
.site-header{position:absolute;left:0;top:0;width:1200px;height:115px;background:var(--white)}
.brand{position:absolute;left:97px;top:18px;display:flex;align-items:center;gap:12px}
.brand-dot{width:34px;height:34px;border-radius:50%;background:var(--navy)}
.brand-name{font-family:"Cinzel",Georgia,serif;font-weight:700;font-size:21px;color:var(--navy);line-height:1.15}
.topbar{position:absolute;right:97px;top:22px;font-size:15px;color:#333;display:flex;align-items:center;gap:14px}
.topbar svg{vertical-align:-2px;margin-right:6px}
.main-nav{position:absolute;right:97px;top:68px;display:flex;gap:30px;align-items:center;font-family:"Cinzel",Georgia,serif;font-size:16px;color:#222}
.main-nav .active{color:var(--accent)}

/* hero */
.hero{position:absolute;left:0;top:115px;width:1200px;height:610px;background:linear-gradient(100deg,#8e8c86 0%,#b9b3a7 35%,#d8cfc2 60%,#a88f7c 100%)}
.hero-kicker{position:absolute;left:100px;top:205px;font-family:"Cinzel",Georgia,serif;font-size:35px;color:var(--white)}
.hero-title{position:absolute;left:100px;top:252px;font-family:"Cinzel",Georgia,serif;font-weight:700;font-size:55px;color:var(--white)}
.btn-outline{position:absolute;left:99px;top:355px;width:197px;height:61px;border:2px solid var(--white);border-radius:31px;color:var(--white);font-weight:700;font-size:17px;display:flex;align-items:center;justify-content:center;letter-spacing:.5px}
.dots{position:absolute;left:566px;top:472px;display:flex;gap:4px}
.dots span{width:13px;height:13px;border:2px solid var(--white);border-radius:50%}
.dots .on{background:var(--white)}
.hero-curve{position:absolute;left:0;bottom:-1px}

/* welcome */
.section-title{position:absolute;left:0;width:1200px;text-align:center;font-family:"Cinzel",Georgia,serif;font-size:40px;color:var(--ink);line-height:57px}
.intro{position:absolute;left:195px;top:893px;width:810px;text-align:center;font-size:14.5px;line-height:28px}
.video{position:absolute;left:400px;top:1044px;width:400px;height:257px;background:linear-gradient(120deg,#6d5a45 0%,#c9bfae 45%,#e7e2da 70%,#9c8c78 100%)}
.play{position:absolute;left:170px;top:98px}
.btn-solid{position:absolute;height:61px;border-radius:31px;background:var(--accent);color:var(--white);font-weight:700;font-size:17px;display:flex;align-items:center;justify-content:center}

/* services */
.services{position:absolute;left:0;top:1466px;width:1200px;height:666px;background:var(--pale)}
.card{position:absolute;top:1684px;width:317px;height:313px;background:var(--white);box-shadow:0 2px 8px rgba(0,0,0,.14);text-align:center}
.card svg{margin-top:36px}
.card h3{font-family:"Cinzel",Georgia,serif;font-weight:400;font-size:23px;line-height:32px;color:var(--ink);margin-top:18px}
.card p{font-size:14.5px;line-height:26px;margin:20px 24px 0}
.card a{display:block;margin-top:16px;font-weight:700;font-size:16px;color:var(--accent-dark);text-decoration:none}
.arrow{position:absolute;top:1816px;width:49px;height:49px;border:2px solid #8a9096;border-radius:50%;background:var(--white);display:flex;align-items:center;justify-content:center}

/* blog */
.post-thumb{position:absolute;top:2282px;width:221px;height:189px;border:1px solid #ccc;padding:5px;background:var(--white)}
.post-thumb div{width:100%;height:100%}
.post{position:absolute;top:2278px;width:240px}
.post h4{font-size:19px;font-weight:600;color:var(--ink)}
.post .meta{font-size:12.5px;color:#444;margin-top:16px;display:flex;align-items:center;gap:6px}
.post p{font-size:14.5px;line-height:24px;margin-top:12px}
.post a{display:block;margin-top:18px;font-weight:700;font-size:14.5px;color:var(--accent-dark);text-decoration:none}

/* footer */
.site-footer{position:absolute;left:0;top:2560px;width:1200px;height:481px;background:var(--navy)}
.foot-brand{position:absolute;left:60px;top:2760px;width:335px;text-align:center;display:flex;flex-direction:column;align-items:center;gap:10px}
.foot-brand .brand-name{color:var(--white);font-size:24px}
.socials{position:absolute;left:146px;top:2848px;display:flex;gap:7px}
.socials span{width:35px;height:35px;border:2px solid var(--white);border-radius:50%}
.foot-col{position:absolute;top:2707px;color:var(--white)}
.foot-col h5{font-family:"Cinzel",Georgia,serif;font-weight:400;font-size:19px;letter-spacing:.5px}
.foot-links{list-style:none;margin-top:20px;font-size:13px;line-height:25.6px}
.contact-row{display:flex;gap:14px;font-size:13px;line-height:25px;margin-top:18px}
.contact-row svg{flex:none;margin-top:5px}
.sub-text{font-size:13px;margin-top:20px}
.email-field{width:276px;height:37px;background:var(--white);border:1px solid #aaa;margin-top:20px;font-size:12px;color:#666;padding:10px 14px}
.btn-sub{width:106px;height:36px;border-radius:18px;background:var(--accent);font-size:12.5px;font-weight:700;margin-top:22px;display:flex;align-items:center;justify-content:center}
.foot-rule{position:absolute;left:99px;top:2949px;width:1002px;height:1px;background:rgba(255,255,255,.35)}
.copyright{position:absolute;left:0;top:2978px;width:1200px;text-align:center;font-size:13px;color:var(--white)}
</style>
</head>
<body>

<header class="site-header">
  <div class="brand">
    <span class="brand-dot"></span>
    <span class="brand-name">QRN Health Partners LLC</span>
  </div>
  <div class="topbar">
    <span><svg width="14" height="14" viewBox="0 0 24 24"><path fill="#2b8fd0" d="M6.6 10.8a15 15 0 0 0 6.6 6.6l2.2-2.2c.3-.3.7-.4 1-.2 1.1.4 2.3.6 3.6.6.6 0 1 .4 1 1V20c0 .6-.4 1-1 1A17 17 0 0 1 3 4c0-.6.4-1 1-1h3.5c.6 0 1 .4 1 1 0 1.3.2 2.5.6 3.6.1.3 0 .7-.2 1z"/></svg>(555) 014-2290</span>
    <span>|</span>
    <span><svg width="15" height="12" viewBox="0 0 24 18"><path fill="#2b8fd0" d="M0 0h24v18H0z"/><path fill="#fff" d="M1 1l11 9 11-9v2L12 12 1 3z"/></svg>info@qrnhealthpartners.com</span>
  </div>
  <nav class="main-nav">
    <span class="active">Home</span><span>About Us</span><span>Services</span><span>Get a quote</span><span>Contact Us</span><span>Staff</span>
    <svg width="16" height="16" viewBox="0 0 24 24"><circle cx="10" cy="10" r="7" fill="none" stroke="#222" stroke-width="3"/><path d="M15 15l7 7" stroke="#222" stroke-width="3.5"/></svg>
  </nav>
</header>

<section class="hero" role="img" aria-label="Photo of a doctor reviewing a tablet with a smiling couple in a bright clinic">
  <div class="hero-kicker">QRN Health Partners</div>
  <div class="hero-title">Advancing Healthcare</div>
  <div class="btn-outline">GET A QUOTE</div>
  <div class="dots"><span class="on"></span><span></span><span></span><span></span></div>
  <svg class="hero-curve" width="1200" height="80" viewBox="0 0 1200 80">
    <path d="M0 62 Q600 -10 1200 62 L1200 80 L0 80Z" fill="#0a3b8f"/>
    <path d="M0 80 Q600 10 1200 80Z" fill="#fff"/>
  </svg>
</section>

<h2 class="section-title" style="top:756px">Welcome to<br>QRN Health Partners</h2>
<p class="intro">QRN Health Partners is a healthcare consulting firm skilled at helping physician practices advance their strategic vision in an ever-evolving healthcare system. QRN Health Partners specializes in revenue cycle optimization, practice management improvement and developing new physician practices. Our technical skills allow us to dig deep into your revenue cycle while our strategic approach ensures we're keeping our eyes on the entire financial picture.</p>

<div class="video" role="img" aria-label="Video still of a doctor handing a document to a patient">
  <svg class="play" width="60" height="60" viewBox="0 0 60 60"><circle cx="30" cy="30" r="30" fill="#111"/><path d="M23 17 L44 30 L23 43Z" fill="#fff"/></svg>
</div>
<div class="btn-solid" style="left:525px;top:1350px;width:150px">ABOUT US</div>

<section class="services">
  <svg class="abs" style="left:0;top:0" width="1200" height="70" viewBox="0 0 1200 70">
    <path d="M0 0 L1200 0 L1200 4 Q600 80 0 4Z" fill="#fff"/>
    <path d="M0 4 Q600 80 1200 4" fill="none" stroke="#c9dbe2" stroke-width="6"/>
  </svg>
  <svg class="abs" style="left:0;bottom:0" width="1200" height="70" viewBox="0 0 1200 70">
    <path d="M0 66 Q600 -10 1200 66 L1200 70 L0 70Z" fill="#fff"/>
    <path d="M0 66 Q600 -10 1200 66" fill="none" stroke="#c9dbe2" stroke-width="6"/>
  </svg>
</section>

<h2 class="section-title" style="top:1590px">Our Services</h2>

<div class="arrow" style="left:26px"><svg width="14" height="20" viewBox="0 0 14 20"><path d="M11 2 L3 10 L11 18" fill="none" stroke="#333" stroke-width="2.5"/></svg></div>
<div class="arrow" style="left:1126px"><svg width="14" height="20" viewBox="0 0 14 20"><path d="M3 2 L11 10 L3 18" fill="none" stroke="#333" stroke-width="2.5"/></svg></div>

<article class="card" style="left:99px">
  <svg width="58" height="52" viewBox="0 0 58 52" fill="#0a3b8f"><circle cx="29" cy="10" r="8"/><circle cx="12" cy="16" r="6"/><circle cx="46" cy="16" r="6"/><path d="M16 44 Q16 22 29 22 Q42 22 42 44Z"/><path d="M1 46 Q1 26 12 26 Q18 26 19 30 Q13 36 13 46Z"/><path d="M57 46 Q57 26 46 26 Q40 26 39 30 Q45 36 45 46Z"/></svg>
  <h3>Revenue<br>Cycle Management</h3>
  <p>Nam libero tempore, cum soluta nobis est eligendi optio cumque nihil imped</p>
  <a>READ MORE</a>
</article>
<article class="card" style="left:442px">
  <svg width="46" height="52" viewBox="0 0 46 52"><rect x="0" y="0" width="46" height="52" rx="4" fill="#0a3b8f"/><rect x="6" y="6" width="34" height="11" fill="#fff"/><g fill="#fff"><rect x="6" y="22" width="7" height="6"/><rect x="19.5" y="22" width="7" height="6"/><rect x="33" y="22" width="7" height="6"/><rect x="6" y="32" width="7" height="6"/><rect x="19.5" y="32" width="7" height="6"/><rect x="33" y="32" width="7" height="6"/><rect x="6" y="42" width="7" height="5"/><rect x="19.5" y="42" width="7" height="5"/><rect x="33" y="42" width="7" height="5"/></g></svg>
  <h3>Medical<br>Billing &amp; Coding</h3>
  <p>Nam libero tempore, cum soluta nobis est eligendi optio cumque nihil imped</p>
  <a>READ MORE</a>
</article>
<article class="card" style="left:782px">
  <svg width="56" height="50" viewBox="0 0 56 50"><path d="M28 0 L56 50 L0 50Z" fill="#0a3b8f"/><rect x="25" y="16" width="6" height="18" fill="#fff"/><rect x="25" y="38" width="6" height="6" fill="#fff"/></svg>
  <h3>Regulatory<br>Compliance</h3>
  <p>Nam libero tempore, cum soluta nobis est eligendi optio cumque nihil imped</p>
  <a>READ MORE</a>
</article>

<h2 class="section-title" style="top:2182px">Latest Blog</h2>

<div class="post-thumb" style="left:97px"><div role="img" aria-label="Photo of a stethoscope, calculator and medical forms on a desk" style="background:linear-gradient(135deg,#3b4550 0%,#9aa3ab 50%,#e6e2da 100%)"></div></div>
<div class="post" style="left:343px">
  <h4>Finibus Bonoret Malorum</h4>
  <div class="meta"><svg width="11" height="11" viewBox="0 0 12 12"><rect x="0" y="1" width="12" height="11" fill="#0a3b8f"/><rect x="1.5" y="4" width="9" height="6.5" fill="#fff"/></svg>17/08/2017 &nbsp;| <svg width="11" height="11" viewBox="0 0 12 12" fill="#0a3b8f"><circle cx="6" cy="3.5" r="3"/><path d="M0 12 Q0 7 6 7 Q12 7 12 12Z"/></svg>John Doe</div>
  <p>Ut enim ad minima veniam, quis nos trum exercitationem ullam corporisu scipit laboriosam, nisi.</p>
  <a>READ MORE</a>
</div>

<div class="post-thumb" style="left:616px"><div role="img" aria-label="Photo of hands typing on a laptop beside a glass of water" style="background:linear-gradient(135deg,#d9d4c8 0%,#b9ad97 45%,#eeeae3 100%)"></div></div>
<div class="post" style="left:864px">
  <h4>Finibus Bonoret Malorum</h4>
  <div class="meta"><svg width="11" height="11" viewBox="0 0 12 12"><rect x="0" y="1" width="12" height="11" fill="#0a3b8f"/><rect x="1.5" y="4" width="9" height="6.5" fill="#fff"/></svg>17/08/2017 &nbsp;| <svg width="11" height="11" viewBox="0 0 12 12" fill="#0a3b8f"><circle cx="6" cy="3.5" r="3"/><path d="M0 12 Q0 7 6 7 Q12 7 12 12Z"/></svg>John Doe</div>
  <p>Ut enim ad minima veniam, quis nos trum exercitationem ullam corporisu scipit laboriosam, nisi.</p>
  <a>READ MORE</a>
</div>

<footer class="site-footer">
  <svg class="abs" style="left:0;top:0" width="1200" height="80" viewBox="0 0 1200 80">
    <path d="M0 0 L1200 0 L1200 8 Q600 70 0 8Z" fill="#fff"/>
    <path d="M0 14 Q600 100 1200 14 L1200 8 Q600 70 0 8Z" fill="#2b8fd0"/>
  </svg>
</footer>

<div class="foot-brand">
  <span class="brand-name">QRN Health Partners LLC</span>
</div>
<div class="socials"><span></span><span></span><span></span><span></span></div>

<div class="foot-col" style="left:424px">
  <h5>Information</h5>
  <ul class="foot-links"><li>Home</li><li>About Us</li><li>Services</li><li>Get a quote</li><li>Contact Us</li><li>Staff</li></ul>
</div>

<div class="foot-col" style="left:594px">
  <h5>Contact Us</h5>
  <div class="contact-row"><svg width="12" height="12" viewBox="0 0 24 24"><path fill="#fff" d="M6.6 10.8a15 15 0 0 0 6.6 6.6l2.2-2.2c.3-.3.7-.4 1-.2 1.1.4 2.3.6 3.6.6.6 0 1 .4 1 1V20c0 .6-.4 1-1 1A17 17 0 0 1 3 4c0-.6.4-1 1-1h3.5c.6 0 1 .4 1 1 0 1.3.2 2.5.6 3.6.1.3 0 .7-.2 1z"/></svg><span>(555) 014-2290</span></div>
  <div class="contact-row"><svg width="13" height="10" viewBox="0 0 24 18"><path fill="#fff" d="M0 0h24v18H0z"/><path fill="#0a3b8f" d="M1 1l11 9 11-9v2L12 12 1 3z"/></svg><span>info@qrnhealthpartners.com</span></div>
  <div class="contact-row"><svg width="10" height="14" viewBox="0 0 10 14"><path fill="#fff" d="M5 0a5 5 0 0 1 5 5c0 4-5 9-5 9S0 9 0 5a5 5 0 0 1 5-5z"/><circle cx="5" cy="5" r="2" fill="#0a3b8f"/></svg><span>180 Harbor Street<br>Brookfield, NY 10099</span></div>
</div>

<div class="foot-col" style="left:825px">
  <h5>Email Subscription</h5>
  <p class="sub-text">Register your email address to get information</p>
  <div class="email-field">Email Address</div>
  <div class="btn-sub">SUBSCRIBE</div>
</div>

<div class="foot-rule"></div>
<p class="copyright">Copyrights © 2018, QRN Health Partners All Rights Reserved.</p>

</body>
</html>
```